Luxury Business Card Design for High-End Window Treatments

Gilded Slatworks
Custom Plantation Shutters & Architectural Shading Systems

⸻

BACK

Daniel Trevick
Owner

Custom Interior & Exterior Window Treatments

919-555-0148
gildedslatworks.com

I have included a picture that I’m hoping we can use on the back, but I’m also wondering if you can get rid of the ladder? Should we get rid of shutters , shades and blinds underneath Gilded Slatworks?

Target Market(s)

High-end residential homeowners, custom home builders, architects, interior designers, and luxury renovation clients seeking premium plantation shutters and motorized architectural shading systems.

Industry/Entity Type

Custom Window treatments

Contact Information for Business Card

Front Gilded Slatworks Custom Plantation Shutters Motorized Architectural Shading Systems BACK Daniel Trevick Owner 919-555-0148 GildedSlatworks.com Custom Interior & Exterior Window Treatments By Appointment

Requirements
Nice to have
• Not 100% sure on nice to halves or the color but you can definitely check out my website to get a better understanding of what I’m trying to do

```html
<!DOCTYPE html>
<html lang="en">
<head>
<meta charset="utf-8">
<title>Gilded Slatworks – Business Card</title>
<link href="https://fonts.googleapis.com/css2?family=Poppins:wght@400;500;700&display=swap" rel="stylesheet">
<style>
  :root {
    --bg: #1b1b1b;
    --card: #141414;
    --card-edge: #222222;
    --gold: #c9a24a;
    --gold-soft: #b8913c;
    --white: #f2f2f2;
    --emboss: #2c2c2c;
    --sky: #6f9bd4;
    --foliage: #4d5a3c;
    --screen: #3a3f46;
  }
  * { margin: 0; padding: 0; box-sizing: border-box; }
  html, body { width: 1200px; height: 875px; overflow: hidden; }
  body {
    background: var(--bg);
    font-family: "Poppins", sans-serif;
    position: relative;
  }
  .card {
    position: absolute;
    left: 320px;
    width: 560px;
    height: 320px;
    background: var(--card);
    border-radius: 18px;
    overflow: hidden;
    border: 1px solid var(--card-edge);
  }
  .card::after {
    content: "";
    position: absolute;
    left: 0; right: 0; bottom: 0;
    height: 5px;
    background: var(--gold);
  }
  .card--front { top: 100px; }
  .card--back { top: 455px; }

  .front-wordmark {
    position: absolute;
    inset: 0;
    display: flex;
    flex-direction: column;
    justify-content: center;
    align-items: center;
    color: var(--emboss);
    font-weight: 500;
    font-size: 52px;
    line-height: 1.05;
    text-align: center;
  }

  .back-wordmark {
    position: absolute;
    left: 40px;
    top: 58px;
    color: var(--gold);
    font-weight: 500;
    font-size: 36px;
    line-height: 1.05;
  }
  .contact {
    position: absolute;
    left: 40px;
    top: 180px;
    color: var(--white);
  }
  .contact__name {
    color: var(--gold);
    font-weight: 700;
    font-size: 20px;
    line-height: 1.1;
  }
  .contact__role {
    font-size: 12px;
    margin-bottom: 10px;
  }
  .contact__line {
    display: flex;
    align-items: center;
    gap: 8px;
    font-size: 13px;
    line-height: 1.6;
  }
  .contact__line--phone { font-weight: 700; }
  .contact__icon { width: 11px; height: 11px; flex: none; }

  .photo-frame {
    position: absolute;
    left: 318px;
    top: 72px;
    width: 200px;
    height: 206px;
    border: 2px solid var(--gold);
    border-top: none;
    border-right: none;
    border-radius: 0 0 0 34px;
  }
  .photo-frame::after {
    content: "";
    position: absolute;
    right: -28px;
    bottom: -2px;
    width: 30px;
    height: 2px;
    background: var(--gold);
  }
  .photo {
    position: absolute;
    left: 334px;
    top: 26px;
    width: 200px;
    height: 214px;
    border-radius: 34px;
    background: linear-gradient(160deg, var(--sky) 0%, var(--foliage) 45%, var(--screen) 75%, #d9d6cf 100%);
  }
</style>
</head>
<body>
  <section class="card card--front" aria-label="Card front">
    <div class="front-wordmark">
      <span>Gilded</span>
      <span>Slatworks</span>
    </div>
  </section>

  <section class="card card--back" aria-label="Card back">
    <div class="back-wordmark">
      <div>Gilded</div>
      <div>Slatworks</div>
    </div>

    <div class="contact">
      <p class="contact__name">Daniel Trevick</p>
      <p class="contact__role">Owner</p>
      <p class="contact__line contact__line--phone">
        <svg class="contact__icon" viewBox="0 0 24 24"><path fill="#c9a24a" d="M6.6 10.8a15.1 15.1 0 0 0 6.6 6.6l2.2-2.2a1 1 0 0 1 1-.25 11.4 11.4 0 0 0 3.6.57 1 1 0 0 1 1 1V20a1 1 0 0 1-1 1A17 17 0 0 1 3 4a1 1 0 0 1 1-1h3.5a1 1 0 0 1 1 1c0 1.25.2 2.45.57 3.57a1 1 0 0 1-.25 1z"/></svg>
        919-555-0148
      </p>
      <p class="contact__line">
        <svg class="contact__icon" viewBox="0 0 24 24"><circle cx="12" cy="12" r="10" fill="none" stroke="#c9a24a" stroke-width="2.4"/><path d="M2 12h20M12 2c3 3 3 17 0 20M12 2c-3 3-3 17 0 20" fill="none" stroke="#c9a24a" stroke-width="2"/></svg>
        gildedslatworks.com
      </p>
    </div>

    <div class="photo-frame"></div>
    <div class="photo" role="img" aria-label="Photo of a two-storey home with screened porch shades under a blue sky and pine trees"></div>
  </section>
</body>
</html>
```